Web Site Design For Real Estate Sales Project

The idea behind this project is pretty simple. I am putting my penthouse apartment up for sale and am trying to be creative in selling it.
Technically this will be pretty simple, it will be 3 pages but graphically this has to be as impressive as possible which is why I am trying Pixel Harbor.
The apartment is located in Barra Da Tijuca, Rio De Janeiro, Brazil. (This is where the 2016 Solstice Meet will be held)
I am looking for an index page and 2 sub-pages. I am open to all kinds of designs and navigation's but it has to make an impression quickly with a professional and enticing design. The index page should make it obvious that there is a penthouse apartment for sale in Barra Da Tijuca ( suburb of Rio De Janeiro). The first sub page is about the Condominium where the apartment is located, the second sub page is about the apartment itself.
Here is a more detailed description of what the 3 pages should be about.
Index Page
This is the landing page and should make it obvious that there is an apartment for sale in Barra Da Tijuca, Rio De Janeiro with the following attributes
251 SQ M
Duplex Penthouse
4 suites
Price R$ 2.200.000
Price per SQ M: R$ 8.764
First Sub-Page
This is about the Condominium which is called "Tranquil Cliff Suites" with the following bullets
*Family friendly and safe
*Direct access to the beach
*Many amenities like pool, football court, gym, sauna
There should be some photos of the condominium and a link to the site of the condominium ( www.tcsqv.com )
Second Sub-page
This is about the apartment. It should list in bullets the features of the apartment and then have a photo gallery of the view and various rooms. I have attached sample photos but will eventually have to use more photos.
Apartment Features
Price: R$ 2.220.000
251 m2 Duplex Penthouse
4 suites
maids room with bath
guest bathroom
living room
dinning room
Terrace with heated pool for year round use
Veranda
As mentioned above I am open to all designs and navigation so feel free to be creative. The important thing is catch peoples attention and get the message across in a few seconds, which is that there is an apartment for sale at this price with these features in this location. I will then use zintra clickreach and SEO to get people to the site.
Thanks
Men and Women from 30-60 years of age.
Apartment

```html
<!DOCTYPE html>
<html lang="en">
<head>
<meta charset="utf-8">
<title>Skyline Barra – Apartment for Sale</title>
<link href="https://fonts.googleapis.com/css2?family=Baumans&family=Cantarell&family=Marcellus&family=Arimo:ital,wght@0,400;0,700;1,400;1,700&display=swap" rel="stylesheet">
<style>
:root{
  --sidebar:#17385a;
  --sidebar-deep:#12304f;
  --accent:#1cb9f0;
  --accent-text:#0d2a47;
  --panel:rgba(8,12,18,.86);
  --white:#ffffff;
  --muted:#d8e2ea;
  --green:#7cc242;
  --divider:rgba(120,190,230,.45);
}
*{box-sizing:border-box;margin:0;padding:0}
html,body{width:1200px;height:676px;overflow:hidden}
body{position:relative;font-family:"Arimo",Arial,sans-serif;color:var(--white);background:#1d3f63}
.hero-photo{
  position:absolute;inset:0;
  background:
    linear-gradient(180deg,#4e86bf 0%,#8fb6d8 17%,#c9dcea 25%,#2d5f8a 28%,#4a6f7e 38%,#7b8a82 52%,#5a7550 68%,#3f6a35 85%,#2f5226 100%);
}
.sidebar{
  position:absolute;left:0;top:0;width:205px;height:676px;
  background:linear-gradient(180deg,var(--sidebar) 0%,var(--sidebar-deep) 100%);
}
.brand{
  height:210px;display:flex;flex-direction:column;align-items:center;justify-content:center;gap:10px;
}
.brand-mark{width:22px;height:22px;border-radius:50%;background:var(--accent)}
.brand-name{
  font-family:"Marcellus",serif;font-size:32px;line-height:1.05;text-align:center;color:var(--white);
}
.main-nav{list-style:none}
.main-nav li{height:51px;display:flex;align-items:center;justify-content:center;position:relative}
.main-nav li:first-child{height:35px;background:var(--accent)}
.main-nav li:not(:first-child)::after{
  content:"";position:absolute;left:50px;right:50px;bottom:0;height:1px;background:var(--divider);
}
.main-nav a{font-family:"Cantarell",sans-serif;font-size:15px;color:var(--white);text-decoration:none}
.main-nav li:first-child a{color:var(--accent-text)}
.copyright{position:absolute;left:28px;top:624px;font-size:12px;font-style:italic}
.listing{
  position:absolute;left:205px;top:210px;width:445px;height:466px;background:var(--panel);padding:0 27px;
}
.listing-head{display:flex;justify-content:space-between;align-items:baseline;margin-top:12px;font-family:"Baumans",sans-serif}
.listing-title{font-size:23px;color:var(--accent);font-weight:400}
.listing-price{font-size:22px;color:var(--white)}
.condo-photo{
  width:400px;height:148px;margin-top:14px;border:2px solid #d9d9d9;
  background:linear-gradient(135deg,#b49a86 0%,#c8b8a8 35%,#7f8a7a 60%,#a9c3d8 100%);
}
.intro{font-size:12px;line-height:1.35;margin-top:15px;color:var(--muted)}
.location{display:flex;gap:14px;align-items:flex-start;margin-top:22px;margin-left:2px;font-size:14px;line-height:1.25}
.specs{display:flex;margin-top:22px}
.spec-list{list-style:none;font-size:12px;line-height:1.25;width:203px;border-right:1px solid var(--divider);padding-right:10px}
.spec-list span{color:var(--accent)}
.contact{padding-left:20px;padding-top:2px}
.phone{display:flex;align-items:center;gap:8px;font-size:24px;font-weight:700;letter-spacing:.5px}
.email{font-size:12px;font-weight:700;margin-top:6px;margin-left:18px}
.details-btn{
  display:inline-block;margin-top:22px;width:123px;height:28px;line-height:28px;text-align:center;
  background:var(--accent);color:var(--accent-text);font-weight:700;font-style:italic;font-size:14px;text-decoration:none;
}
</style>
</head>
<body>
<div class="hero-photo" role="img" aria-label="Aerial view of Barra Da Tijuca coastline, beach, lagoons and mountains under a blue sky"></div>

<aside class="sidebar">
  <div class="brand">
    <span class="brand-mark"></span>
    <span class="brand-name">Skyline<br>Barra</span>
  </div>
  <ul class="main-nav">
    <li><a href="#">Home</a></li>
    <li><a href="#">Tranquil Cliff Suites</a></li>
    <li><a href="#">About the Apartment</a></li>
    <li><a href="#">Contact Us</a></li>
  </ul>
  <p class="copyright">© 2013. All Right Reserved</p>
</aside>

<main class="listing">
  <header class="listing-head">
    <h1 class="listing-title">Apartment for Sale</h1>
    <span class="listing-price">R$ 2.200.000</span>
  </header>
  <div class="condo-photo" role="img" aria-label="Entrance of the Tranquil Cliff Suites condominium with gated driveway"></div>
  <p class="intro">The apartment is located in Barra Da Tijuca, Rio De Janeiro, Brazil.<br>(This is where the 2016 Solstice Meet will be held)</p>
  <div class="location">
    <svg width="20" height="30" viewBox="0 0 20 30" aria-hidden="true"><path d="M10 0C4.5 0 0 4.4 0 9.8 0 17 10 30 10 30s10-13 10-20.2C20 4.4 15.5 0 10 0z" fill="var(--green)"/><circle cx="10" cy="9.5" r="4" fill="#0b1118"/></svg>
    <p>Barra Da Tijuca, Rio De Janeiro with the<br>following attributes</p>
  </div>
  <div class="specs">
    <ul class="spec-list">
      <li><span>Building Size</span> : 251 SQ M</li>
      <li><span>Property Type</span> : Duplex Penthouse</li>
      <li><span>No. of Suites</span> : 4 suites</li>
      <li><span>Price per SQ M</span> : R$ 8.764</li>
    </ul>
    <div class="contact">
      <div class="phone">
        <svg width="24" height="20" viewBox="0 0 24 20" aria-hidden="true"><path d="M2 7c0-4 20-4 20 0v2h-5V6.5c-3-1-7-1-10 0V9H2z" fill="var(--green)"/><path d="M6 10h12l3 9H3z" fill="var(--green)"/><circle cx="12" cy="14" r="2.5" fill="#0b1118"/></svg>
        <span>742 316 908</span>
      </div>
      <p class="email">info@skyline-barra.com</p>
    </div>
  </div>
  <a class="details-btn" href="#">VIEW DETAILS</a>
</main>
</body>
</html>
```